1" x 3" label needed for essential oil bottle(s) - new ecommerce company

We need a label designed for 10 ml bottles of essential oils. We are offering 9 different types of essential oil: Lavender, Cedarwood, Eucalyptus, Frankincense, Lemon, Orange, Peppermint, Rosemary, and Tea Tree. The label should have a space for the type of essential oil. The bottles are an amber color (am including a photo) as essential oils are sensitive to light. also am including an AI file of our logo, which we'd like included on the label; the logo file also contains our logo colors, a dark blue and light grey. We'd also like the following on the label: "CAUTION: EYE AND SKIN IRRITANT. Avoid contact with eyes and skin. Wash hands after handling. If eye contact occurs, flush with water for 15 minutes. Not intended for topical or internal use. Contains Essential Oils. KEEP OUT OF REACH OF CHILDREN."
Also "Ingredients: 100% pure essential oil, GC tested."
Also "0.33 fl oz (10 ml)
Finally, we will need to include a sideways bar code on the right side of the label, so need 3/8" of white space on the right of the label.
We'd like the label to be calming, but modern, friendly, and confident.

```html
<!DOCTYPE html>
<html lang="en">
<head>
<meta charset="utf-8">
<title>Solenna Cedarwood Labels</title>
<link rel="stylesheet" href="https://fonts.googleapis.com/css2?family=Cormorant+Garamond:wght@500&family=Montserrat:wght@500;600;700&display=swap">
<style>
  :root {
    --backdrop: #f3f2f0;
    --terracotta: #b9694a;
    --speck: #d99a7b;
    --cocoa: #5a2a1f;
    --white: #fbf3ec;
    --navy: #1f2f4a;
    --mist: #dcdde0;
    --barcode-white: #ffffff;
  }
  * { margin: 0; padding: 0; box-sizing: border-box; }
  html, body {
    width: 1200px; height: 863px; overflow: hidden;
    background: var(--backdrop);
  }
  .label-row {
    position: absolute; top: 216px; left: 0;
    width: 1200px;
    display: flex; justify-content: center; gap: 50px;
  }
  .label {
    position: relative;
    width: 330px; height: 430px;
    background: var(--terracotta);
    overflow: hidden;
    font-family: "Montserrat", sans-serif;
  }
  .barcode-space {
    position: absolute; top: 0; right: 0; bottom: 0;
    width: 42px;
    background: var(--barcode-white);
  }
  .speckles { position: absolute; top: 0; left: 0; }
  .brand-vertical {
    position: absolute; top: 40px; height: 230px;
    display: flex; align-items: center; justify-content: center;
    width: 44px;
    font-family: "Cormorant Garamond", serif;
    font-weight: 500; font-size: 30px; letter-spacing: 7px;
    writing-mode: vertical-rl;
    white-space: nowrap;
  }
  .brand-vertical.reads-up { transform: rotate(180deg); }
  .brand-vertical.right { left: 232px; }
  .brand-vertical.left { left: 16px; }
  .emblem { position: absolute; }
  .oil-name { font-weight: 700; font-size: 19px; letter-spacing: 2.5px; }
  .purity { font-weight: 600; font-size: 11px; letter-spacing: 0.8px; margin-top: 5px; }
  .volume { font-weight: 600; font-size: 10px; letter-spacing: 0.5px; margin-top: 12px; }

  .safety {
    position: absolute; left: 22px; width: 244px; top: 300px;
    font-size: 7.5px; font-weight: 500; line-height: 1.4; letter-spacing: 0.1px;
  }
  .safety strong { font-weight: 700; }
  .safety .ingredients { margin-top: 6px; }

  /* Variant one */
  .label--classic .brand-vertical,
  .label--classic .copy,
  .label--classic .safety { color: var(--white); }
  .label--classic .emblem { top: 72px; left: 30px; }
  .label--classic .copy { position: absolute; left: 30px; top: 168px; }
  .label--classic .purity { line-height: 1.35; }

  /* Variants two and three */
  .label--filled .brand-vertical,
  .label--outlined .brand-vertical,
  .label--filled .copy,
  .label--outlined .copy,
  .label--filled .safety,
  .label--outlined .safety { color: var(--cocoa); }
  .label--filled .emblem,
  .label--outlined .emblem { top: 62px; left: 130px; }
  .label--filled .copy,
  .label--outlined .copy {
    position: absolute; left: 66px; width: 220px; top: 180px;
    text-align: center;
  }
  .label--filled .oil-name,
  .label--outlined .oil-name { font-weight: 600; font-size: 17px; }
  .label--filled .purity,
  .label--outlined .purity { font-weight: 500; font-size: 9.5px; }
  .label--filled .volume,
  .label--outlined .volume { font-weight: 500; font-size: 9.5px; margin-top: 14px; }
  .label--filled .safety,
  .label--outlined .safety { text-align: center; }
</style>
</head>
<body>
  <main class="label-row">
    <section class="label label--classic">
      <svg class="speckles" width="288" height="430" aria-hidden="true">
        <g fill="var(--speck)">
          <circle cx="150" cy="44" r="2"/><circle cx="60" cy="70" r="1.5"/>
          <circle cx="200" cy="130" r="1.5"/><circle cx="112" cy="150" r="2"/>
          <circle cx="180" cy="240" r="1.5"/><circle cx="40" cy="410" r="2"/>
          <circle cx="220" cy="418" r="1.5"/><circle cx="140" cy="272" r="1.5"/>
        </g>
      </svg>
      <svg class="emblem" width="64" height="64" aria-hidden="true">
        <circle cx="32" cy="32" r="31" fill="var(--mist)"/>
      </svg>
      <div class="copy">
        <div class="oil-name">CEDARWOOD</div>
        <div class="purity">100% Pure<br>Essential Oil</div>
        <div class="volume">0.33 fl oz (10 ml)</div>
      </div>
      <div class="brand-vertical right">SOLENNA</div>
      <div class="safety">
        <p><strong>CAUTION: EYE AND SKIN IRRITANT.</strong> Avoid contact with eyes and skin. Wash hands after handling. If eye contact occurs, flush with water for 15 minutes. Not intended for topical or internal use. Contains Essential Oils. <strong>KEEP OUT OF REACH OF CHILDREN.</strong></p>
        <p class="ingredients"><strong>Ingredients:</strong> 100% pure essential oil, GC tested.</p>
      </div>
      <div class="barcode-space"></div>
    </section>

    <section class="label label--filled">
      <div class="brand-vertical left reads-up">SOLENNA</div>
      <svg class="emblem" width="92" height="92" aria-hidden="true">
        <circle cx="46" cy="46" r="45" fill="var(--navy)"/>
      </svg>
      <div class="copy">
        <div class="oil-name">CEDARWOOD</div>
        <div class="purity">100% Pure Essential Oil</div>
        <div class="volume">0.33 fl oz (10 ml)</div>
      </div>
      <div class="safety">
        <p><strong>CAUTION: EYE AND SKIN IRRITANT.</strong> Avoid contact with eyes and skin. Wash hands after handling. If eye contact occurs, flush with water for 15 minutes. Not intended for topical or internal use. Contains Essential Oils. <strong>KEEP OUT OF REACH OF CHILDREN.</strong></p>
        <p class="ingredients"><strong>Ingredients:</strong> 100% pure essential oil, GC tested.</p>
      </div>
      <div class="barcode-space"></div>
    </section>

    <section class="label label--outlined">
      <div class="brand-vertical left">SOLENNA</div>
      <svg class="emblem" width="92" height="92" aria-hidden="true">
        <circle cx="46" cy="46" r="44" fill="none" stroke="var(--navy)" stroke-width="2"/>
      </svg>
      <div class="copy">
        <div class="oil-name">CEDARWOOD</div>
        <div class="purity">100% Pure Essential Oil</div>
        <div class="volume">0.33 fl oz (10 ml)</div>
      </div>
      <div class="safety">
        <p><strong>CAUTION: EYE AND SKIN IRRITANT.</strong> Avoid contact with eyes and skin. Wash hands after handling. If eye contact occurs, flush with water for 15 minutes. Not intended for topical or internal use. Contains Essential Oils. <strong>KEEP OUT OF REACH OF CHILDREN.</strong></p>
        <p class="ingredients"><strong>Ingredients:</strong> 100% pure essential oil, GC tested.</p>
      </div>
      <div class="barcode-space"></div>
    </section>
  </main>
</body>
</html>
```